Varelko App for Smart Devices IoT WiFi Electronic

Varelko is a siren manufacturer. This application is used for the company's products that have a Wi-Fi connection and an internet connection, which can be configured and activated remotely through this application. In addition, this application is used to activate the siren at specific times for the start and end of shifts in companies and schools. Users will be siren installers and IT or HR managers.
In addition to activating motorized sirens timers, some siren models have speakers and allow you to play TTS (text to speech) audio, audio recorded by the user on the phone and upload audio (mp3) with playlist programming with start and end times.
Application screens: home with dashboard (one dashboard for each category). Device categories: timers, speakers, motorized siren. Screen for requesting evaluation in the Play Store. Screen for registering the user profile. Screen for registering devices according to their category (timers, speakers, motorized siren). Screen for registering device groups. Screen for pairing the device on the client's Wi-Fi network. Screen for registering activation times. Screen for uploading MP3 audios. Screen for registering playlists with audio selection, start and end times. Screen for recording audio for later sending to the speakers. Screen for converting text to speech and sending to the speakers. It is important to have a time picker with the day of the week to program the activation times and playlist.

Target Market(s)

Schools, Companies and Stores.

Industry/Entity Type

IoT

Font styles to use
Sans Serif
Other font styles liked:
• roboto

Colors
FFC000
F8CF3A
FAE287
FDF2CF
FEFAEE

Requirements
Must have
• time picker with weekdays for timer programming feature.
Nice to have
• app review request screen on play store

```html
<!DOCTYPE html>
<html lang="en">
<head>
<meta charset="utf-8">
<title>Varelko – siren timer app screens</title>
<link href="https://fonts.googleapis.com/css2?family=Roboto:wght@400;500;700&display=swap" rel="stylesheet">
<style>
:root{
  --amber:#FFC000;
  --gold:#F8CF3A;
  --sand:#FAE287;
  --cream:#FDF2CF;
  --ivory:#FEFAEE;
  --ink:#1f1f1f;
  --ink-soft:#3a3a3a;
  --line:#9a9a9a;
  --stage:#8c8c8c;
  --dark:#222222;
}
*{box-sizing:border-box;margin:0;padding:0}
html,body{width:1200px;height:787px;overflow:hidden}
body{background:var(--stage);font-family:"Roboto",sans-serif;color:var(--ink);position:relative}
.screen{position:absolute;width:251px;height:596px;background:linear-gradient(180deg,#fff 0%,var(--ivory) 40%,#fff 100%);overflow:hidden}
.screen *{position:absolute}
.app-header{left:0;top:0;width:100%;height:60px;border-bottom:4px solid var(--amber);background:#fff}
.brand{left:13px;top:12px;font-size:29px;font-weight:500;color:var(--amber);letter-spacing:.3px;line-height:1}
.hdr-wifi{width:22px;height:22px;border-radius:50%;background:#2b2b2b;top:18px}
.hdr-grid,.hdr-user{top:18px}
.bottom-bar{left:6px;right:6px;bottom:0;height:10px;background:var(--amber);border-radius:12px 12px 0 0}
.heading{left:0;width:100%;text-align:center;font-size:15px;font-weight:400}
.label{left:18px;font-size:11.5px}
.field{left:18px;width:215px;height:28px;border:1px solid var(--line);background:#fff;font-size:8.5px;padding-left:15px;line-height:26px}
.toggle{width:14px;height:9px;border:1.2px solid #333;border-radius:5px;background:#e6e6e6}
.toggle::after{content:"";position:absolute;left:1.5px;top:1px;width:4.5px;height:4.5px;border:1px solid #333;border-radius:50%}
.card{left:16px;width:198px;border:1px solid #b9b9b9;background:#fff}
.card .when{left:19px;top:10px;font-size:9px}
.card .note{left:19px;font-size:7.6px;color:var(--ink-soft)}
.card .clock{right:11px;top:7px}
.card .pen{right:13px}
.small{font-size:8.5px}
</style>
</head>
<body>

<!-- Screen 1: dashboard -->
<section class="screen" style="left:76px;top:159px;width:231px;height:548px">
  <header class="app-header" style="height:59px">
    <div class="brand" style="top:14px;font-size:27px">Varelko</div>
    <div class="hdr-wifi" style="left:144px;top:18px"></div>
    <svg class="hdr-grid" style="left:164px;top:20px" width="20" height="16" viewBox="0 0 20 16"><g fill="none" stroke="#333" stroke-width="1"><rect x="1" y="1" width="3" height="3"/><rect x="6" y="1" width="3" height="3"/><rect x="11" y="1" width="3" height="3"/><rect x="1" y="6" width="3" height="3"/><rect x="6" y="6" width="3" height="3"/><rect x="11" y="6" width="3" height="3"/><rect x="1" y="11" width="3" height="3"/><rect x="6" y="11" width="3" height="3"/><rect x="11" y="11" width="3" height="3"/><path d="M15 7l2 2 2-2"/></g></svg>
    <svg class="hdr-user" style="left:202px;top:18px" width="18" height="18" viewBox="0 0 18 18"><g fill="none" stroke="#222" stroke-width="1.3"><circle cx="9" cy="9" r="8"/><circle cx="9" cy="7" r="3"/><path d="M3.5 14.5c1.5-2.5 9.5-2.5 11 0"/></g></svg>
  </header>
  <div style="left:16px;top:78px;font-size:11px">Motorized sirens timers</div>
  <div class="card" style="top:104px;height:44px">
    <div style="left:10px;top:7px;width:18px;height:18px;border-radius:50%;background:var(--cream)"></div>
    <svg style="left:13px;top:11px" width="12" height="10" viewBox="0 0 12 10"><g fill="none" stroke="#d99a00" stroke-width="1"><circle cx="6" cy="5" r="1.4"/><path d="M3.5 2.5a3.5 3.5 0 000 5M8.5 2.5a3.5 3.5 0 010 5M1.5 1a6 6 0 000 8M10.5 1a6 6 0 010 8"/></g></svg>
    <div style="left:37px;top:8px;font-size:10px">Shift Timing</div>
    <div style="left:37px;top:26px;font-size:7.6px;color:var(--ink-soft)">Activate the device for shift timing</div>
    <div class="toggle" style="right:11px;top:8px"></div>
  </div>
  <svg style="left:16px;top:164px" width="11" height="11" viewBox="0 0 11 11"><g fill="none" stroke="var(--amber)" stroke-width="1.2"><circle cx="5.5" cy="5.5" r="4.6"/><path d="M5.5 3v2.7l1.8 1"/></g></svg>
  <div style="left:36px;top:164px;font-size:10.5px">Schedules</div>
  <svg style="left:202px;top:163px" width="12" height="12" viewBox="0 0 12 12"><circle cx="6" cy="6" r="6" fill="var(--amber)"/><path d="M6 3v6M3 6h6" stroke="#222" stroke-width="1.2"/></svg>

  <div class="card" style="top:183px;height:71px">
    <div class="when">9:00 AM to 1:00 PM&nbsp;&nbsp; Weekdays</div>
    <div class="note" style="top:26px">1st half session</div>
    <div style="left:19px;top:41px;font-size:8.6px">Audio: text to speech</div>
    <div class="note" style="top:56px">The shfit has be started, Have a nice day</div>
    <svg class="clock" width="10" height="10" viewBox="0 0 10 10"><g fill="none" stroke="#444" stroke-width="1"><circle cx="5" cy="5" r="4.3"/><path d="M5 2.5V5l1.6 1"/></g></svg>
    <svg class="pen" style="top:25px" width="8" height="8" viewBox="0 0 8 8"><path d="M1 7l.4-1.8L5.8.8l1.4 1.4L2.8 6.6z" fill="#222"/></svg>
  </div>
  <div class="card" style="top:259px;height:45px">
    <div class="when">1:00 PM to 2:00 PM&nbsp;&nbsp; Weekdays</div>
    <div class="note" style="top:27px">Lunch Time</div>
    <svg class="clock" width="10" height="10" viewBox="0 0 10 10"><g fill="none" stroke="#444" stroke-width="1"><circle cx="5" cy="5" r="4.3"/><path d="M5 2.5V5l1.6 1"/></g></svg>
    <svg class="pen" style="top:26px" width="8" height="8" viewBox="0 0 8 8"><path d="M1 7l.4-1.8L5.8.8l1.4 1.4L2.8 6.6z" fill="#222"/></svg>
  </div>
  <div class="card" style="top:310px;height:45px">
    <div class="when">4:00 PM to 4:20 PM&nbsp;&nbsp; Weekdays</div>
    <div class="note" style="top:27px">Coffee Break</div>
    <svg class="clock" width="10" height="10" viewBox="0 0 10 10"><g fill="none" stroke="#444" stroke-width="1"><circle cx="5" cy="5" r="4.3"/><path d="M5 2.5V5l1.6 1"/></g></svg>
    <svg class="pen" style="top:26px" width="8" height="8" viewBox="0 0 8 8"><path d="M1 7l.4-1.8L5.8.8l1.4 1.4L2.8 6.6z" fill="#222"/></svg>
  </div>
  <div class="card" style="top:361px;height:45px">
    <div class="when">6:00 PM&nbsp;&nbsp; Weekdays</div>
    <div class="note" style="top:27px">Signing out Time</div>
    <svg class="clock" width="10" height="10" viewBox="0 0 10 10"><g fill="none" stroke="#444" stroke-width="1"><circle cx="5" cy="5" r="4.3"/><path d="M5 2.5V5l1.6 1"/></g></svg>
    <svg class="pen" style="top:26px" width="8" height="8" viewBox="0 0 8 8"><path d="M1 7l.4-1.8L5.8.8l1.4 1.4L2.8 6.6z" fill="#222"/></svg>
  </div>
  <div class="card" style="top:412px;height:45px">
    <div class="when">9:00 AM to 12 PM&nbsp;&nbsp; Weekend</div>
    <div class="note" style="top:27px">Special Session</div>
    <svg class="clock" width="10" height="10" viewBox="0 0 10 10"><g fill="none" stroke="#444" stroke-width="1"><circle cx="5" cy="5" r="4.3"/><path d="M5 2.5V5l1.6 1"/></g></svg>
    <svg class="pen" style="top:26px" width="8" height="8" viewBox="0 0 8 8"><path d="M1 7l.4-1.8L5.8.8l1.4 1.4L2.8 6.6z" fill="#222"/></svg>
  </div>

  <svg style="left:16px;top:477px" width="12" height="12" viewBox="0 0 12 12"><circle cx="6" cy="6" r="6" fill="var(--amber)"/><circle cx="6" cy="6" r="3.2" fill="none" stroke="#fff" stroke-width="1"/></svg>
  <div style="left:36px;top:477px;font-size:10.5px;font-weight:500">Status</div>
  <div style="left:16px;top:495px;font-size:8.6px;line-height:14.5px;width:210px">Next Ring of siren is at 1:00 PM to 2:00 PM<br>which is lunch time (Siren alarm in 20 mins)</div>
  <div class="bottom-bar" style="left:4px;right:4px"></div>
</section>

<!-- Screen 2: add schedule -->
<section class="screen" style="left:349px;top:74px">
  <header class="app-header">
    <div class="brand">Varelko</div>
    <div class="hdr-wifi" style="left:157px"></div>
    <svg class="hdr-grid" style="left:188px;top:20px" width="20" height="16" viewBox="0 0 20 16"><g fill="none" stroke="#333" stroke-width="1"><rect x="1" y="1" width="3" height="3"/><rect x="6" y="1" width="3" height="3"/><rect x="11" y="1" width="3" height="3"/><rect x="1" y="6" width="3" height="3"/><rect x="6" y="6" width="3" height="3"/><rect x="11" y="6" width="3" height="3"/><rect x="1" y="11" width="3" height="3"/><rect x="6" y="11" width="3" height="3"/><rect x="11" y="11" width="3" height="3"/><path d="M15 7l2 2 2-2"/></g></svg>
    <svg class="hdr-user" style="left:219px" width="19" height="19" viewBox="0 0 18 18"><g fill="none" stroke="#222" stroke-width="1.3"><circle cx="9" cy="9" r="8"/><circle cx="9" cy="7" r="3"/><path d="M3.5 14.5c1.5-2.5 9.5-2.5 11 0"/></g></svg>
  </header>
  <div class="heading" style="top:81px">Add the new schedules for siren</div>
  <div class="label" style="top:116px">Title of Siren alarm</div>
  <div class="field" style="top:137px">Enter</div>
  <div class="label" style="top:173px">Start time of siren</div>
  <div class="field" style="top:194px">Time</div>
  <div class="label" style="top:231px">End time of siren</div>
  <div class="field" style="top:252px">Time</div>
  <div style="left:6px;top:297px;width:239px;height:29px;background:var(--gold)">
    <div style="left:15px;top:7px;font-size:11.5px">Week:</div>
    <div style="left:117px;top:8px;font-size:8.6px">Weekdays</div>
    <div class="toggle" style="left:170px;top:10px;background:var(--sand)"></div>
    <div style="left:188px;top:8px;font-size:8.6px">Weekend</div>
  </div>
  <div class="label" style="top:341px">Audio Format</div>
  <div class="field" style="top:363px">MP3 Audio
    <svg style="right:12px;top:10px" width="8" height="6" viewBox="0 0 8 6"><path d="M1 1l3 3 3-3" fill="none" stroke="#222" stroke-width="1.2"/></svg>
  </div>
  <div style="left:18px;top:391px;width:215px;height:48px;border:1px solid #ddd;border-top:none;background:#fff">
    <div style="left:15px;top:7px;font-size:9.5px">Text-to-Speech</div>
    <div style="left:7px;top:21px;width:200px;height:19px;background:#f2efe8"></div>
    <div style="left:15px;top:23px;font-size:9.5px">Audio Recording</div>
  </div>
  <div class="label" style="top:449px">choose audio from files</div>
  <div style="left:18px;top:469px;font-size:9.5px;font-weight:500">MP3 Audio</div>
  <div class="field" style="top:490px">choose audio from files
    <svg style="right:10px;top:6px" width="12" height="15" viewBox="0 0 12 15"><g fill="none" stroke="#222" stroke-width="1"><path d="M4 5H1v9h10V5H8M6 10V1M3.5 3.5L6 1l2.5 2.5"/></g></svg>
  </div>
  <div style="left:86px;top:533px;width:79px;height:32px;border-radius:16px;background:var(--dark);color:#fff;font-size:11.5px;font-weight:500;text-align:center;line-height:32px">ADD</div>
  <div class="bottom-bar"></div>
</section>

<!-- Screen 3: available devices -->
<section class="screen" style="left:619px;top:117px">
  <header class="app-header" style="height:63px">
    <div class="brand" style="top:14px">Varelko</div>
    <div class="hdr-wifi" style="left:157px;top:20px"></div>
    <svg class="hdr-grid" style="left:188px;top:23px" width="20" height="16" viewBox="0 0 20 16"><g fill="none" stroke="#333" stroke-width="1"><rect x="1" y="1" width="3" height="3"/><rect x="6" y="1" width="3" height="3"/><rect x="11" y="1" width="3" height="3"/><rect x="1" y="6" width="3" height="3"/><rect x="6" y="6" width="3" height="3"/><rect x="11" y="6" width="3" height="3"/><rect x="1" y="11" width="3" height="3"/><rect x="6" y="11" width="3" height="3"/><rect x="11" y="11" width="3" height="3"/><path d="M15 7l2 2 2-2"/></g></svg>
    <svg class="hdr-user" style="left:219px;top:20px" width="19" height="19" viewBox="0 0 18 18"><g fill="none" stroke="#222" stroke-width="1.3"><circle cx="9" cy="9" r="8"/><circle cx="9" cy="7" r="3"/><path d="M3.5 14.5c1.5-2.5 9.5-2.5 11 0"/></g></svg>
  </header>
  <div class="heading" style="top:80px">Devices Available to connect</div>
  <div class="field" style="top:124px">Xyz timer<div class="toggle" style="right:8px;top:8px"></div></div>
  <div class="field" style="top:163px">IT Siren abc<div class="toggle" style="right:8px;top:8px"></div></div>
  <div class="field" style="top:203px">Support team speaker<div class="toggle" style="right:8px;top:8px"></div></div>
  <div class="bottom-bar"></div>
</section>

<!-- Screen 4: wifi pairing -->
<section class="screen" style="left:889px;top:74px">
  <header class="app-header">
    <div class="brand">Varelko</div>
    <div class="hdr-wifi" style="left:157px"></div>
    <svg class="hdr-grid" style="left:188px;top:20px" width="20" height="16" viewBox="0 0 20 16"><g fill="none" stroke="#333" stroke-width="1"><rect x="1" y="1" width="3" height="3"/><rect x="6" y="1" width="3" height="3"/><rect x="11" y="1" width="3" height="3"/><rect x="1" y="6" width="3" height="3"/><rect x="6" y="6" width="3" height="3"/><rect x="11" y="6" width="3" height="3"/><rect x="1" y="11" width="3" height="3"/><rect x="6" y="11" width="3" height="3"/><rect x="11" y="11" width="3" height="3"/><path d="M15 7l2 2 2-2"/></g></svg>
    <svg class="hdr-user" style="left:219px" width="19" height="19" viewBox="0 0 18 18"><g fill="none" stroke="#222" stroke-width="1.3"><circle cx="9" cy="9" r="8"/><circle cx="9" cy="7" r="3"/><path d="M3.5 14.5c1.5-2.5 9.5-2.5 11 0"/></g></svg>
  </header>
  <div class="heading" style="top:93px;line-height:20px">you will be connecting to<br>Xyz timer to your account<br>using wi-fi pairing</div>
  <svg style="left:0;top:185px" width="251" height="70" viewBox="0 0 251 70">
    <g fill="none" stroke="var(--amber)" stroke-width="4"><circle cx="58" cy="33" r="29"/><circle cx="192" cy="33" r="29"/></g>
    <g fill="none" stroke="#111" stroke-width="2"><circle cx="58" cy="33" r="13"/><circle cx="58" cy="29" r="4.5"/><path d="M49.5 42c3-4.5 14-4.5 17 0"/></g>
    <g fill="none" stroke="#111" stroke-width="2.4"><path d="M197 24.5a11 11 0 11-8-1.8"/><path d="M192 33l5-7"/></g>
    <g fill="none" stroke="#444" stroke-width=".8"><circle cx="91" cy="33" r="1"/><circle cx="102" cy="33" r="1.4"/><circle cx="113" cy="33" r="1.8"/><circle cx="124" cy="33" r="2.2"/><circle cx="135" cy="33" r="2.6"/><circle cx="146" cy="33" r="3"/><circle cx="157" cy="33" r="3.2"/></g>
  </svg>
  <div style="left:38px;top:259px;width:40px;text-align:center;font-size:15px">abc</div>
  <div style="left:150px;top:259px;width:84px;text-align:center;font-size:15px">Xyz timer</div>
  <div class="bottom-bar"></div>
</section>

</body>
</html>
```